Ridgeline Orchards Organic Cherry POS card 7x11

We are wanting to create a one-sided 7 x 11 organic cherry card that is eye catching and informative.This should be clear and easy to read and not cluttered. We use these cards as a display in grocery stores, demo stands, and other events to market Organic Ridgeline Sweet Orchards. We have a few facts that we would like displayed on the card (see attachment).

Target Market(s)

Consumers

Industry/Entity Type

Agriculture

Requirements
Must have
• Natural color palettes
• Easy to read
• Ridgeline Orchards
Nice to have
• Unique, realistic cherry design

```html
<!DOCTYPE html>
<html lang="en">
<head>
<meta charset="utf-8">
<title>Ridgeline Orchards – Organic Cherry Card</title>
<link rel="stylesheet" href="https://fonts.googleapis.com/css2?family=Amatic+SC:wght@700&family=Patrick+Hand+SC&family=Open+Sans:wght@700&display=swap">
<style>
  :root {
    --page: #eeeae2;
    --leaf-dark: #2f6a12;
    --leaf: #4f9a1e;
    --leaf-light: #7cbf3a;
    --cherry: #8e0d18;
    --cherry-deep: #4a070c;
    --band-top: #141a14;
    --band-light: rgba(236, 236, 230, 0.82);
    --headline-green: #1d7a2a;
    --ink: #1d1d1d;
    --white: #ffffff;
  }
  * { margin: 0; padding: 0; box-sizing: border-box; }
  html, body { width: 1200px; height: 1200px; overflow: hidden; background: var(--page); }
  .card {
    position: absolute; left: 50px; top: 250px;
    width: 1100px; height: 700px; overflow: hidden;
    box-shadow: 0 6px 18px rgba(0,0,0,0.25);
  }
  .card__photo {
    position: absolute; inset: 0;
    background:
      radial-gradient(ellipse 45% 60% at 25% 75%, var(--cherry) 0%, var(--cherry-deep) 55%, transparent 80%),
      radial-gradient(ellipse 18% 22% at 62% 42%, #d92b3a 0%, transparent 100%),
      linear-gradient(110deg, var(--leaf-dark) 0%, var(--leaf) 55%, var(--leaf-light) 100%);
  }
  .card__topband {
    position: absolute; left: 0; top: 0; width: 100%; height: 36px;
    background: var(--band-top);
  }
  .card__header {
    position: absolute; left: 0; top: 36px; width: 100%; height: 160px;
    background: var(--band-light);
    display: flex; align-items: center; justify-content: space-between;
    padding: 0 50px 0 34px;
  }
  .headline {
    font-family: "Patrick Hand SC", cursive;
    color: var(--headline-green);
    font-size: 38px; line-height: 1.05; letter-spacing: 1px;
    max-width: 640px;
  }
  .brand {
    display: flex; align-items: center; gap: 16px;
    font-family: "Patrick Hand SC", cursive;
    font-size: 56px; color: var(--ink); line-height: 1;
  }
  .brand__dot { width: 54px; height: 54px; border-radius: 50%; background: var(--cherry); }
  .benefits {
    position: absolute; right: 58px; top: 290px;
    list-style: none; text-align: right;
    font-family: "Amatic SC", sans-serif; font-weight: 700;
    color: var(--white); font-size: 62px; line-height: 1.0;
  }
  .footnote {
    position: absolute; right: 58px; bottom: 26px; text-align: right;
    font-family: "Open Sans", sans-serif; font-weight: 700;
    color: var(--white); font-size: 20px; line-height: 1.2; text-transform: uppercase;
  }
  .footnote strong { font-size: 32px; }
</style>
</head>
<body>
  <section class="card">
    <div class="card__photo" role="img" aria-label="Photograph of a wire basket full of ripe red cherries with a jar of cherry preserves topped by a red polka-dot cloth, against a blurred green orchard"></div>
    <div class="card__topband"></div>
    <header class="card__header">
      <h1 class="headline">Washington State is the nation’s largest producer of organic cherries</h1>
      <div class="brand"><span class="brand__dot"></span><span class="brand__name">Ridgeline Orchards</span></div>
    </header>
    <ul class="benefits">
      <li>Fat Free</li>
      <li>Source of Vitamin C</li>
      <li>Source of Melatonin</li>
      <li>Source of Potassium</li>
      <li>A Natural Anti-Inflammatory</li>
    </ul>
    <p class="footnote"><strong>Organic</strong> Ridgeline Orchards cherries<br>make up 1/3 of the nation’s production</p>
  </section>
</body>
</html>
```